Home Remodeling company needs a business card design

we need a business card design for home remodeling company in hamilton county, indiana USA. we offers a wide range of construction services including whole house renovations, Design and Build Basements and Kitchen and Bathroom Remodeling . we would like to see designs for both site of business card that use the same color of the company logo and also including all information below :
1- Karim Feltous CEO / General Contractor
2- all company contacts Telephone numbers ( 1-888-DULOM-47 ) ( 317-555-0193) email address ( info@dulomhome.com) website ( www.dulomhome.com ) and social media logos (Facebook- twitter- google plus )
3- company logo
4- licensed . insured . bonded

```html
<!DOCTYPE html>
<html lang="en">
<head>
<meta charset="utf-8">
<title>DULOM Home Remodeling — Business Card</title>
<link href="https://fonts.googleapis.com/css2?family=Montserrat:wght@800&family=Roboto:wght@400;700&display=swap" rel="stylesheet">
<style>
  :root {
    --stage: #e4e2e0;
    --charcoal: #333334;
    --charcoal-deep: #2a2a2b;
    --paper: #f4f4f4;
    --red: #c7252f;
    --ink: #2b2b2b;
    --muted: #5a5a5a;
    --logo-light: #d9d9d9;
  }
  * { box-sizing: border-box; margin: 0; padding: 0; }
  html, body { width: 1200px; height: 716px; overflow: hidden; }
  body {
    background: var(--stage);
    font-family: "Roboto", Arial, sans-serif;
    position: relative;
  }
  .card {
    position: absolute;
    top: 209px;
    width: 520px;
    height: 298px;
    border-radius: 4px;
    overflow: hidden;
    box-shadow: 0 6px 18px rgba(0,0,0,.18);
  }
  .card--front { left: 50px; background: var(--charcoal); }
  .card--back { left: 630px; background: var(--paper); }

  .brand {
    position: absolute;
    display: flex;
    align-items: flex-start;
    gap: 10px;
    font-family: "Montserrat", Arial, sans-serif;
    font-weight: 800;
  }
  .brand__mark { width: 12px; height: 12px; margin-top: 14px; }
  .brand__name { font-size: 58px; line-height: 1; letter-spacing: 1px; }
  .brand__tag { font-size: 15px; letter-spacing: 5.5px; margin-top: 4px; }

  .card--front .brand { left: 92px; top: 100px; color: var(--logo-light); }
  .card--front .brand__mark { background: var(--logo-light); }

  .card--back .brand { left: 26px; top: 38px; color: var(--ink); }
  .card--back .brand__mark { background: var(--red); }
  .card--back .brand__name { font-size: 50px; }
  .card--back .brand__tag { font-size: 13px; letter-spacing: 4.6px; color: var(--ink); }

  .wave { position: absolute; inset: 0; }

  .person { position: absolute; left: 26px; top: 142px; }
  .person__name { color: var(--red); font-weight: 700; font-size: 19px; }
  .person__role { color: var(--muted); font-size: 12.5px; margin-top: 3px; }
  .social { display: flex; gap: 4px; margin-top: 9px; }
  .social span { width: 16px; height: 16px; background: var(--charcoal); border-radius: 2px; }

  .credentials {
    position: absolute; right: 22px; top: 58px;
    color: #f2f2f2; font-size: 14px; line-height: 1.45; text-align: right;
  }

  .contacts { position: absolute; left: 262px; top: 188px; list-style: none; }
  .contacts li {
    display: flex; align-items: center; gap: 12px;
    font-size: 15px; color: var(--ink); line-height: 24px;
    white-space: nowrap;
  }
  .contacts svg { width: 13px; height: 13px; fill: var(--red); flex: none; }
</style>
</head>
<body>

<section class="card card--front" aria-label="Card front">
  <div class="brand">
    <span class="brand__mark"></span>
    <div>
      <div class="brand__name">DULOM</div>
      <div class="brand__tag">HOME REMODELING</div>
    </div>
  </div>
</section>

<section class="card card--back" aria-label="Card back">
  <svg class="wave" viewBox="0 0 520 298" preserveAspectRatio="none" aria-hidden="true">
    <path d="M240,0 C330,0 385,55 425,135 C455,195 482,222 520,230 L520,0 Z" fill="var(--charcoal-deep)"/>
    <path d="M175,20 C280,4 350,45 400,128 C435,192 470,228 520,242" fill="none" stroke="var(--red)" stroke-width="4"/>
    <path d="M220,4 C310,-2 360,42 408,120" fill="none" stroke="var(--red)" stroke-width="2"/>
  </svg>

  <div class="brand">
    <span class="brand__mark"></span>
    <div>
      <div class="brand__name">DULOM</div>
      <div class="brand__tag">HOME REMODELING</div>
    </div>
  </div>

  <div class="person">
    <div class="person__name">Karim Feltous</div>
    <div class="person__role">CEO / General Contractor</div>
    <div class="social" aria-label="Social media"><span></span><span></span><span></span></div>
  </div>

  <div class="credentials">Licensed «<br>Bonded «<br>Insured «</div>

  <ul class="contacts">
    <li><svg viewBox="0 0 24 24"><path d="M6.6 10.8a15 15 0 006.6 6.6l2.2-2.2a1 1 0 011-.25 11.4 11.4 0 003.6.57 1 1 0 011 1V20a1 1 0 01-1 1A17 17 0 013 4a1 1 0 011-1h3.5a1 1 0 011 1c0 1.25.2 2.45.57 3.57a1 1 0 01-.25 1z"/></svg>1-888-DULOM-47</li>
    <li><svg viewBox="0 0 24 24"><rect x="3" y="9" width="18" height="11" rx="2"/><rect x="7" y="3" width="10" height="6"/></svg>317-555-0193</li>
    <li><svg viewBox="0 0 24 24"><path d="M2 5h20v14H2z M3 6l9 7 9-7" /></svg>info@dulomhome.com</li>
    <li><svg viewBox="0 0 24 24"><circle cx="12" cy="12" r="10"/></svg>www.dulomhome.com</li>
  </ul>
</section>

</body>
</html>
```